Business Card Design for Training Business

Clear Path Coaching is a new business that delivers training and other services with a focus on topics related to mental health and wellbeing, for example, Wellmind Response Course, Resilience etc. We have a strong focus on evidence-based psychology and neuroscience. I have a logo which I will upload with the brief, so please consider colours that work well with the logo.
Target Market(s)
Adults, workplaces (particularly government and not-for-profits)
Industry/Entity Type
Business
Contact Information for Business Card
Head Strong TrainingSamantha SellwoodDirector0438 770 850sam@headstrongtraining.com.auwww.headstrongtraining.com.au

```html
<!DOCTYPE html>
<html lang="en">
<head>
<meta charset="utf-8">
<title>Clear Path Coaching – Business Card</title>
<link rel="stylesheet" href="https://fonts.googleapis.com/css2?family=Open+Sans:wght@300;400&display=swap">
<style>
  :root {
    --stage: #ece9e4;
    --card: #ffffff;
    --teal: #3a9a9c;
    --teal-light: #9fd6d8;
    --wordmark: #7a6f69;
    --ink: #141414;
  }
  * { margin: 0; padding: 0; box-sizing: border-box; }
  html, body {
    width: 1200px; height: 892px; overflow: hidden;
    background: var(--stage);
    font-family: "Open Sans", sans-serif;
  }
  .card {
    position: absolute; left: 75px; top: 146px;
    width: 1050px; height: 600px;
    background: var(--card);
    box-shadow: 0 10px 30px rgba(0,0,0,0.18);
    overflow: hidden;
  }
  .band-art { position: absolute; inset: 0; }
  .brand {
    position: absolute; left: 120px; top: 34px; width: 320px;
    text-align: center; color: var(--wordmark); font-weight: 300;
  }
  .brand-dot {
    display: block; width: 112px; height: 112px; margin: 0 auto 14px;
    border-radius: 50%; background: var(--teal-light);
  }
  .brand-name { font-size: 40px; letter-spacing: 6px; line-height: 1.05; text-transform: uppercase; }
  .brand-sub { font-size: 18px; letter-spacing: 9px; text-transform: uppercase; }
  .person { position: absolute; left: 70px; top: 268px; }
  .person-name { color: var(--teal); font-size: 44px; font-weight: 400; }
  .person-role { color: var(--ink); font-size: 24px; margin-top: -2px; }
  .contacts { list-style: none; position: absolute; left: 40px; top: 400px; }
  .contacts li {
    display: flex; align-items: center; gap: 14px;
    font-size: 25px; color: var(--ink); line-height: 40px;
  }
  .contacts svg { width: 24px; height: 24px; flex: none; }
</style>
</head>
<body>
  <section class="card">
    <svg class="band-art" viewBox="0 0 1050 600" aria-hidden="true">
      <path d="M777 0 L924 0 Q880 300 745 600 L578 600 Q720 300 777 0 Z" fill="var(--teal)"/>
      <circle cx="766" cy="330" r="158" fill="var(--card)"/>
      <circle cx="766" cy="330" r="148" fill="none" stroke="var(--teal)" stroke-width="11"/>
      <circle cx="766" cy="330" r="122" fill="var(--teal-light)" opacity="0.35"/>
    </svg>

    <header class="brand">
      <span class="brand-dot"></span>
      <div class="brand-name">Clear Path</div>
      <div class="brand-sub">Coaching</div>
    </header>

    <div class="person">
      <h1 class="person-name">Rebecca Tanfield</h1>
      <p class="person-role">Director</p>
    </div>

    <ul class="contacts">
      <li>
        <svg viewBox="0 0 24 24"><rect width="24" height="24" fill="var(--ink)"/><path d="M8 5 L10 9 L8.5 10.5 Q10 14 13.5 15.5 L15 14 L19 16 L17.5 19 Q9 18 5 7 Z" fill="#fff"/></svg>
        0491 362 517
      </li>
      <li>
        <svg viewBox="0 0 24 24"><rect width="24" height="24" fill="var(--ink)"/><rect x="4" y="7" width="16" height="11" fill="#fff"/><path d="M4 7 L12 13 L20 7" fill="none" stroke="var(--ink)" stroke-width="1.5"/></svg>
        bec@clearpathcoaching.example.au
      </li>
      <li>
        <svg viewBox="0 0 24 24"><rect width="24" height="24" fill="var(--ink)"/><circle cx="12" cy="12" r="7" fill="none" stroke="#fff" stroke-width="1.6"/><path d="M5 12 H19 M12 5 Q8 12 12 19 Q16 12 12 5" fill="none" stroke="#fff" stroke-width="1.4"/></svg>
        www.clearpathcoaching.example.au
      </li>
    </ul>
  </section>
</body>
</html>
```